Brochure/flyer for our trip to Paris

Our company is taking us all on a summer trip to Paris. We have some key information that we need to tell everybody about the trip. We think a nicely designed brochure or flyer, which uses our brand colours and guidelines, would be something nice to keep during the trip and as a memento afterwards.

We are looking for a brochure or a flyer which contains all the info in the attached document.

This needs to happen really fast as we actually go to Paris on the 13th August. We also need time to print it!

We can provide a library of icons. All images in the document can be changed. you don't have to use the images in the document.

Target Market(s)

People in our company. They are fun and as this is for a party the flyer needs to feel uplifting.

Industry/Entity Type

Health

Font styles to use
Other font styles liked:
• Nexa - please see attached font.

Requirements
Must have
• Designers must stick to our brand guideline, font and the colours we use.
• Please also see attached content for the flyer.
• This website shows our style - https://www.lorventi.com/fr
Should not have
• Please don't make it too tacky or too much about French things. It can be a bit playful but not too much.

```html
<!DOCTYPE html>
<html lang="en">
<head>
<meta charset="utf-8">
<title>Paris Trip – Travel &amp; Hotel Information</title>
<link rel="stylesheet" href="https://fonts.googleapis.com/css2?family=Outfit:wght@500;600&family=Questrial&display=swap">
<style>
  :root {
    --navy: #3a4b98;
    --teal: #6bc3c4;
    --orange: #ea5a2d;
    --sky: #4085c8;
    --white: #ffffff;
    --map-base: #e6e4df;
    --map-road: #d6d3cc;
  }
  * { margin: 0; padding: 0; box-sizing: border-box; }
  html, body { width: 773px; height: 1200px; overflow: hidden; }
  body {
    position: relative;
    background: var(--navy);
    color: var(--white);
    font-family: "Questrial", "Helvetica Neue", Arial, sans-serif;
    font-size: 22.4px;
    line-height: 28px;
  }
  .brand-strip { position: absolute; left: 705px; width: 68px; }
  .brand-strip--teal { top: 300px; height: 300px; background: var(--teal); }
  .brand-strip--orange { top: 600px; height: 300px; background: var(--orange); }
  .brand-strip--sky { top: 900px; height: 300px; background: var(--sky); }

  .section-title {
    position: absolute;
    left: 52px;
    font-family: "Outfit", "Helvetica Neue", Arial, sans-serif;
    font-weight: 500;
    font-size: 57px;
    line-height: 64px;
    letter-spacing: 0.5px;
  }
  .section-title--travel { top: 40px; }
  .section-title--hotel { top: 550px; }

  .block { position: absolute; left: 52px; }
  .journey-heading { display: block; }
  .journey-list { list-style: none; margin-top: 28px; }
  .journey-list li { position: relative; padding-left: 70px; width: 590px; }
  .journey-list li::before { content: "-"; position: absolute; left: 0; }
  .journey-list strong { font-family: "Outfit", sans-serif; font-weight: 600; }

  .journey--outward { top: 130px; }
  .journey--return { top: 356px; }

  .hotel-address { top: 642px; font-style: normal; }
  .hotel-tel { top: 811px; }
  .hotel-metro { top: 868px; }

  .hotel-map {
    position: absolute;
    left: 52px; top: 922px;
    width: 466px; height: 226px;
    background: linear-gradient(135deg, var(--map-base), #f2e6cf 60%, var(--map-road));
  }
</style>
</head>
<body>
  <div class="brand-strip brand-strip--teal"></div>
  <div class="brand-strip brand-strip--orange"></div>
  <div class="brand-strip brand-strip--sky"></div>

  <h1 class="section-title section-title--travel">Travel Information</h1>

  <section class="block journey--outward">
    <span class="journey-heading">Outward Journey 13/08/16:</span>
    <ul class="journey-list">
      <li>Meet at Kings Cross St Pancras International Station no later than <strong>6:55am</strong>.</li>
      <li>Our train departs at 7:55am and arrives in Paris at 11:17am local time.</li>
    </ul>
  </section>

  <section class="block journey--return">
    <span class="journey-heading">Return Journey 14/08/16:</span>
    <ul class="journey-list">
      <li>Meet at Gare Du Nord no later than <strong>2:00 pm</strong>.</li>
      <li>Our train departs at 3:13pm and arrives in London at 4:30pm local time.</li>
    </ul>
  </section>

  <h2 class="section-title section-title--hotel">Hotel Information</h2>

  <address class="block hotel-address">
    HOTEL DES TILLEULS<br>
    &nbsp;12, rue des Lavandières<br>
    75001<br>
    Paris<br>
    France
  </address>

  <p class="block hotel-tel">Tel: +33 1 40 00 00 00</p>
  <p class="block hotel-metro">Nearest Metro Station: Châtelet &nbsp;(As Pictured)</p>

  <div class="hotel-map" role="img" aria-label="Street map around Châtelet metro station on Rue de Rivoli"></div>
</body>
</html>
```